SANDWICH SKILLET DESIGN (Packaging)

We require a skillet (sandwich box) designed I have uploaded a similar one we have already
I have uploaded the logo to be placed on the skillet
( BRIGHT MEADOW DELI HAWKS LTD)
we would like a sandwich skillet which has a white background and maybe some veg items which maybe found in a sandwich
hope this helps

```html
<!DOCTYPE html>
<html lang="en">
<head>
<meta charset="utf-8">
<title>Sandwich Skillet – Bright Meadow Deli Hawks Ltd</title>
<link rel="stylesheet" href="https://fonts.googleapis.com/css2?family=Oswald:wght@400;600&display=swap">
<style>
  :root {
    --backdrop: #c8c6c6;
    --board: #e4e3e3;
    --board-light: #f1f0f0;
    --wine: #861a2e;
    --stripe: #f6f5f5;
    --window: #d2c8ab;
    --window-edge: #b9b2a0;
    --ink: #333333;
    --ink-soft: #5a5458;
    --veg-red: #c8392c;
    --veg-green: #6f9a4a;
    --veg-purple: #8a4a86;
    --bread: #d9a45a;
  }
  * { margin: 0; padding: 0; box-sizing: border-box; }
  html, body { width: 770px; height: 1200px; overflow: hidden; }
  body {
    background: var(--backdrop);
    font-family: "Oswald", "Arial Narrow", sans-serif;
  }
  .dieline {
    position: absolute;
    left: 0; top: 0;
    width: 770px; height: 1200px;
    display: flex;
    align-items: center;
    justify-content: center;
    gap: 22px;
  }
  .panel { display: block; }
  .panel--side { align-self: center; margin-top: 36px; }
  .board { fill: var(--board); }
  .band { fill: var(--wine); }
  .stripe { fill: var(--stripe); }
  .window { fill: var(--window); stroke: var(--window-edge); stroke-width: 0.8; }
  .seal { fill: #ffffff; stroke: var(--wine); stroke-width: 0.8; }
  .seal-name { fill: var(--wine); font-weight: 400; font-size: 3.6px; letter-spacing: 0.1px; }
  .product-title { fill: var(--ink); font-weight: 600; font-size: 7.2px; letter-spacing: 0.2px; }
  .storage-note { fill: var(--ink-soft); font-weight: 400; font-size: 3.3px; }
  .storage-temp { fill: var(--wine); font-weight: 400; font-size: 3.3px; }
  .allergens { fill: var(--ink-soft); font-weight: 400; font-size: 4.6px; letter-spacing: 0.1px; }
  .company { fill: var(--wine); font-weight: 400; font-size: 4.6px; letter-spacing: 0.1px; }
</style>
</head>
<body>
<main class="dieline">

  <!-- Triangular side panel -->
  <svg class="panel panel--side" width="337" height="333" viewBox="0 0 293 290" aria-label="Skillet side panel">
    <defs>
      <linearGradient id="vegTones" x1="0" y1="0" x2="1" y2="1">
        <stop offset="0" stop-color="var(--veg-red)"/>
        <stop offset="0.3" stop-color="var(--bread)"/>
        <stop offset="0.55" stop-color="var(--veg-green)"/>
        <stop offset="0.75" stop-color="var(--veg-purple)"/>
        <stop offset="1" stop-color="var(--veg-green)"/>
      </linearGradient>
    </defs>
    <polygon class="board" points="0,0 293,290 6,290"/>
    <polygon role="img" aria-label="Photograph of fresh salad vegetables: tomatoes, cucumber slices, red cabbage and bread crust"
             points="1,120 168,165 293,290 6,290" fill="url(#vegTones)" opacity="0.92"/>
    <g class="brand-seal">
      <circle class="seal" cx="50" cy="242" r="22"/>
      <text class="seal-name" x="50" y="240" text-anchor="middle" style="font-size:5px">BRIGHT MEADOW DELI</text>
      <text class="seal-name" x="50" y="247" text-anchor="middle" style="font-size:5px">HAWKS LTD</text>
    </g>
  </svg>

  <!-- Front panel with window -->
  <svg class="panel panel--front" width="168" height="383" viewBox="0 0 146 333" aria-label="Skillet front panel">
    <rect class="board" x="0" y="0" width="146" height="333"/>
    <path class="band" d="M0 0 H146 V36 Q72 30 0 46 Z"/>
    <path class="stripe" d="M0 46 Q72 30 146 36 V44 Q72 40 0 56 Z"/>
    <path class="band" d="M0 56 Q72 40 146 44 V52 Q72 49 0 65 Z"/>
    <path class="window" d="M30 70 Q76 60 122 66 Q136 68 136 82 V252 Q136 264 124 264 Q100 266 97 285 Q95 297 84 297 H30 Q16 297 16 283 V84 Q16 70 30 70 Z"/>
    <g class="brand-seal">
      <circle class="seal" cx="118" cy="282" r="15"/>
      <text class="seal-name" x="118" y="281" text-anchor="middle">BRIGHT MEADOW</text>
      <text class="seal-name" x="118" y="286" text-anchor="middle">DELI HAWKS LTD</text>
    </g>
    <text class="product-title" x="73" y="313" text-anchor="middle">FRESHLY HANDMADE SANDWICHES</text>
    <text class="storage-note" x="73" y="320" text-anchor="middle">EAT ON DAY OF PURCHASE KEEP REFRIGERATED</text>
    <text class="storage-temp" x="73" y="325" text-anchor="middle">BELOW 5°C</text>
  </svg>

  <!-- Back panel with allergen and company details -->
  <svg class="panel panel--back" width="172" height="383" viewBox="0 0 150 333" aria-label="Skillet back panel">
    <rect class="board" x="0" y="0" width="150" height="333"/>
    <path class="band" d="M0 0 H150 V36 Q74 30 0 46 Z"/>
    <path class="stripe" d="M0 46 Q74 30 150 36 V44 Q74 40 0 56 Z"/>
    <path class="band" d="M0 56 Q74 40 150 44 V52 Q74 49 0 65 Z"/>
    <g class="brand-seal">
      <circle class="seal" cx="82" cy="222" r="17"/>
      <text class="seal-name" x="82" y="221" text-anchor="middle">BRIGHT MEADOW</text>
      <text class="seal-name" x="82" y="226" text-anchor="middle">DELI HAWKS LTD</text>
    </g>
    <text class="allergens" x="86" y="256" text-anchor="middle">MAY CONTAIN LUPIN, MOLLUSCS</text>
    <text class="allergens" x="86" y="262" text-anchor="middle">MILK,BARLEY, SESAME SEEDS</text>
    <text class="allergens" x="86" y="268" text-anchor="middle">CRUSTACEANS,FISH,SULPHITES,SOYA</text>
    <text class="allergens" x="86" y="274" text-anchor="middle">CELERY &amp; NUTS</text>
    <text class="company" x="86" y="286" text-anchor="middle">BRIGHT MEADOW DELI HAWKS LTD</text>
    <text class="company" x="86" y="292" text-anchor="middle">UNIT 4 LARK ROW</text>
    <text class="company" x="86" y="298" text-anchor="middle">HK12 7PL</text>
  </svg>

</main>
</body>
</html>
```